High-End Print/Digital Ad for Unique Luxury Travel Company Required

Objective:
Design a compelling and visually striking advertisement that highlights our company’s unmatched luxury travel experiences. The ad should elevate our brand image, spark curiosity, and drive prospective clients to contact us.
Target Audience:
• Affluent individuals seeking extraordinary, tailor-made travel experiences
• Affluent, luxury, high-net-worth individuals looking for value, expertise, and white-glove service
• Professionals or retirees who appreciate unique, thoughtfully curated travel over mainstream tourism
Key Messages to Communicate:
• One-of-a-kind luxury travel: Once-in-a-lifetime experiences that are curated with creativity and meticulous attention to detail
• Exceptional service: White-glove, personalized planning from start to finish
• 38 years’ travel experience – expert knowledge of destinations, modes of travel, premium accommodations and well-established, meaningful industry connections.
• Highly trusted: Cruise line executives often say, “No one does what you do.”
Tone and Style:
• Elegant, luxurious, sophisticated
• Eye-catching, polished, and modern
• Professional but warm—conveys trust and credibility
• High-impact visuals (full-bleed imagery, custom graphics, or high-end photography)
Deliverables:
• One full-page print ad and digital ad
• Ready-to-print, high-resolution file + working file (PSD, AI, etc.)
Optional: Social media-optimized version or short motion-graphic variation (if designer offers it)
Inspiration & Visual Style Suggestions:
• Think Lumen Voyages, Harrow Pike Wanderer, Silver Quill, or Orvel Retreats ad styles
• Large, emotive imagery with elegant typography
• Clean layout that speaks luxury, clarity, and trust
Copy Direction (draft):
For those who’ve explored the world—and crave something beyond the ordinary.
Each journey is a masterfully curated experience, rich in detail, seamless in execution, and unforgettable in every way.
Founded in 1997, Tidewell Journeys is a unique travel company specializing in cruising, all-inclusive luxury properties, and tours world-wide for individuals, groups, and incentives.
We offer an exceptional range of services designed to ensure every journey is flawlessly executed and truly unforgettable.
Let us help you plan your next extraordinary adventure.
Note: You may refine the copy slightly based on layout or format needs.
Other Resources for References:
1. Website - www.tidewelljourneys-example.com

```html
<!DOCTYPE html>
<html lang="en">
<head>
<meta charset="utf-8">
<title>Tidewell Journeys — Print and Digital Ad</title>
<link href="https://fonts.googleapis.com/css2?family=Playfair+Display:wght@400;600;700;800&family=Poppins:wght@300;400;500;600&family=Great+Vibes&display=swap" rel="stylesheet">
<style>
  :root {
    --board: #8eadd7;
    --paper: #ffffff;
    --brand-blue: #174a86;
    --ink: #1c1c1c;
    --body-ink: #2b2b2b;
    --gold: #c9a54a;
    --faint: #eef1f5;
  }
  * { margin: 0; padding: 0; box-sizing: border-box; }
  html, body { width: 1200px; height: 898px; overflow: hidden; }
  body {
    background: var(--board);
    position: relative;
    font-family: "Poppins", sans-serif;
    color: var(--ink);
  }
  .format-label {
    position: absolute; top: 38px;
    font-family: "Poppins", sans-serif; font-size: 17px; font-weight: 400;
    color: #ffffff; transform: translateX(-50%); white-space: nowrap;
  }
  .format-label b { font-weight: 600; }
  .ad {
    position: absolute; background: var(--paper); overflow: hidden;
    box-shadow: 0 14px 30px rgba(30, 55, 100, 0.28);
  }
  .ad--print { left: 48px; top: 80px; width: 544px; height: 768px; }
  .ad--digital { left: 609px; top: 80px; width: 544px; height: 543px; }
  .ad > * { position: absolute; }

  .watermark {
    font-family: "Playfair Display", serif; font-weight: 600;
    color: var(--faint); white-space: nowrap; line-height: 1; z-index: 0;
  }
  .brand {
    display: flex; align-items: center; gap: 8px;
    font-family: "Playfair Display", serif; font-weight: 400;
    color: var(--brand-blue); text-transform: uppercase; letter-spacing: 0.5px; white-space: nowrap;
  }
  .brand__dot { border-radius: 50%; background: var(--brand-blue); flex: none; }

  .lead { font-family: "Poppins", sans-serif; font-weight: 400; transform: translateX(-50%); white-space: nowrap; }
  .headline { font-family: "Playfair Display", serif; font-weight: 800; color: var(--brand-blue); line-height: 1; white-space: nowrap; }
  .subhead { font-family: "Playfair Display", serif; font-weight: 700; color: var(--ink); line-height: 1; letter-spacing: -1px; white-space: nowrap; }
  .amp { font-family: "Great Vibes", cursive; color: var(--ink); line-height: 1; }
  .crave-box {
    border: 1.5px solid var(--brand-blue);
    display: flex; align-items: center; justify-content: center;
    font-family: "Poppins", sans-serif; font-weight: 400; color: var(--brand-blue); white-space: nowrap;
  }
  .beyond { font-family: "Playfair Display", serif; font-weight: 600; color: var(--ink); transform: translateX(-50%); white-space: nowrap; }
  .body-copy { font-family: "Poppins", sans-serif; font-weight: 300; color: var(--body-ink); z-index: 1; }
  .founded { font-family: "Playfair Display", serif; font-weight: 600; color: var(--brand-blue); }

  .photo { z-index: 1; display: block; }
  .photo--framed { outline: 1px solid var(--gold); }

  .help-band {
    background: var(--brand-blue); color: #ffffff; z-index: 2;
    font-family: "Playfair Display", serif; font-weight: 700; letter-spacing: -0.5px;
    display: flex; align-items: center; justify-content: center;
    transform: rotate(-3.5deg); white-space: nowrap;
  }
  .plan { font-family: "Poppins", sans-serif; font-weight: 400; transform: translateX(-50%); white-space: nowrap; z-index: 1; }
  .adventure {
    font-family: "Playfair Display", serif; font-weight: 700; color: var(--brand-blue);
    transform: translateX(-50%); white-space: nowrap; line-height: 1; letter-spacing: -1.5px; z-index: 1;
  }
  .site {
    display: flex; align-items: center; gap: 6px; white-space: nowrap; z-index: 2;
    font-family: "Poppins", sans-serif; font-weight: 400; transform: translateX(-50%);
  }
  .site__dot { border-radius: 50%; flex: none; }
</style>
</head>
<body>

<div class="format-label" style="left:319px;"><b>PRINT AD</b> “8.27 x 11.69” Inches</div>
<div class="format-label" style="left:880px;"><b>DIGITAL AD</b> “1080x1080” Pixels</div>

<!-- Print ad -->
<section class="ad ad--print">
  <div class="watermark" style="left:-8px; top:670px; font-size:190px;">Adventure</div>

  <div class="brand" style="left:27px; top:46px; font-size:25px;">
    <span class="brand__dot" style="width:24px; height:24px;"></span>Tidewell Journeys
  </div>

  <div class="lead" style="left:153px; top:114px; font-size:18px;">For those who’ve</div>
  <div class="headline" style="left:26px; top:134px; font-size:64px; letter-spacing:-3px;">Explored</div>
  <div class="subhead" style="right:268px; top:192px; font-size:34px;">The World</div>
  <div class="amp" style="left:24px; top:208px; font-size:72px;">&amp;</div>
  <div class="crave-box" style="left:63px; top:229px; width:202px; height:41px; font-size:21px;">Crave Something</div>
  <div class="beyond" style="left:158px; top:279px; font-size:23.5px;">Beyond the Ordinary.</div>

  <p class="body-copy" style="left:27px; top:333px; width:270px; font-size:12.6px; line-height:16.5px;">
    Each journey is a masterfully curated experience, rich in detail, seamless in execution, &amp; unforgettable in every way.
  </p>

  <svg class="photo" role="img" aria-label="Felucca sailboat on the Nile at sunset with pyramids behind" style="left:310px; top:93px;" width="209" height="292">
    <defs>
      <linearGradient id="nileBase" x1="0" y1="0" x2="0" y2="1">
        <stop offset="0" stop-color="#d89a4e"/>
        <stop offset="0.3" stop-color="#f2c77a"/>
        <stop offset="0.55" stop-color="#e3ac64"/>
        <stop offset="0.66" stop-color="#8a9a5a"/>
        <stop offset="0.78" stop-color="#3f9c98"/>
        <stop offset="1" stop-color="#1d6f80"/>
      </linearGradient>
      <radialGradient id="nileSun" cx="0.35" cy="0.35" r="0.55">
        <stop offset="0" stop-color="#fff1c4" stop-opacity="0.9"/>
        <stop offset="1" stop-color="#fff1c4" stop-opacity="0"/>
      </radialGradient>
    </defs>
    <rect width="209" height="292" fill="url(#nileBase)"/>
    <rect width="209" height="292" fill="url(#nileSun)"/>
  </svg>

  <svg class="photo photo--framed" role="img" aria-label="Traveller dining on a cliffside terrace above a Mediterranean coastal village" style="left:26px; top:411px;" width="269" height="193">
    <defs>
      <linearGradient id="coastBase" x1="0" y1="0" x2="0" y2="1">
        <stop offset="0" stop-color="#f2f3f1"/>
        <stop offset="0.22" stop-color="#dfe4e6"/>
        <stop offset="0.4" stop-color="#8fa8b8"/>
        <stop offset="0.7" stop-color="#5f89a0"/>
        <stop offset="1" stop-color="#6b6148"/>
      </linearGradient>
      <radialGradient id="coastCliff" cx="0.88" cy="0.62" r="0.45">
        <stop offset="0" stop-color="#a88566" stop-opacity="0.85"/>
        <stop offset="1" stop-color="#a88566" stop-opacity="0"/>
      </radialGradient>
    </defs>
    <rect width="269" height="193" fill="url(#coastBase)"/>
    <rect width="269" height="193" fill="url(#coastCliff)"/>
  </svg>

  <div class="help-band" style="left:65px; top:601px; width:176px; height:40px; font-size:23px;">Let us help you</div>

  <div class="plan" style="left:153px; top:660px; font-size:17.5px;">Plan your Next Extraordinary</div>
  <div class="adventure" style="left:153px; top:680px; font-size:48px;">Adventure.</div>

  <div class="founded" style="left:316px; top:410px; font-size:14.5px;">Founded in 1997,</div>
  <p class="body-copy" style="left:316px; top:433px; width:205px; font-size:12.6px; line-height:16.5px;">
    Tidewell Journeys is a unique travel company specializing in cruising, all-inclusive luxury properties, &amp; tours world-wide for individuals, groups, and incentives.
  </p>
  <p class="body-copy" style="left:316px; top:539px; width:205px; font-size:12.6px; line-height:16.5px;">
    We offer an exceptional range of services designed to ensure every journey is flawlessly executed &amp; truly unforgettable.
  </p>

  <svg class="photo" role="img" aria-label="Northern lights over a snowy mountain valley with a stag by a river" style="left:304px; top:626px;" width="215" height="117">
    <defs>
      <linearGradient id="auroraBase" x1="0" y1="0" x2="0" y2="1">
        <stop offset="0" stop-color="#0d2c49"/>
        <stop offset="0.55" stop-color="#1b4a72"/>
        <stop offset="1" stop-color="#0c2643"/>
      </linearGradient>
      <radialGradient id="auroraGlow" cx="0.55" cy="0.25" r="0.5">
        <stop offset="0" stop-color="#4fe3b0" stop-opacity="0.85"/>
        <stop offset="1" stop-color="#4fe3b0" stop-opacity="0"/>
      </radialGradient>
      <radialGradient id="auroraPink" cx="0.5" cy="0.5" r="0.22">
        <stop offset="0" stop-color="#e6a4c4" stop-opacity="0.55"/>
        <stop offset="1" stop-color="#e6a4c4" stop-opacity="0"/>
      </radialGradient>
    </defs>
    <rect width="215" height="117" fill="url(#auroraBase)"/>
    <rect width="215" height="117" fill="url(#auroraGlow)"/>
    <rect width="215" height="117" fill="url(#auroraPink)"/>
  </svg>
  <div class="site" style="left:411px; top:713px; font-size:11px; color:#ffffff;">
    <span class="site__dot" style="width:12px; height:12px; background:#ffffff;"></span>tidewelljourneys-example.com
  </div>
</section>

<!-- Digital ad -->
<section class="ad ad--digital">
  <div class="watermark" style="left:-10px; top:465px; font-size:150px;">Adventure</div>

  <div class="brand" style="left:27px; top:36px; font-size:20px;">
    <span class="brand__dot" style="width:20px; height:20px;"></span>Tidewell Journeys
  </div>

  <div class="lead" style="left:148px; top:88px; font-size:16.5px;">For those who’ve</div>
  <div class="headline" style="left:27px; top:104px; font-size:56px; letter-spacing:-2.5px;">Explored</div>
  <div class="subhead" style="right:290px; top:156px; font-size:31px;">The World</div>
  <div class="amp" style="left:24px; top:170px; font-size:60px;">&amp;</div>
  <div class="crave-box" style="left:60px; top:190px; width:183px; height:38px; font-size:19px;">Crave Something</div>
  <div class="beyond" style="left:141px; top:235px; font-size:21.5px;">Beyond the Ordinary.</div>

  <svg class="photo photo--framed" role="img" aria-label="Hot air balloons above ancient colossus statues in a desert valley" style="left:26px; top:284px;" width="248" height="156">
    <defs>
      <linearGradient id="balloonBase" x1="0" y1="0" x2="0" y2="1">
        <stop offset="0" stop-color="#5f93c6"/>
        <stop offset="0.4" stop-color="#c9dbe6"/>
        <stop offset="0.58" stop-color="#e8d2b0"/>
        <stop offset="0.72" stop-color="#c98e5e"/>
        <stop offset="1" stop-color="#a89781"/>
      </linearGradient>
      <radialGradient id="balloonGlow" cx="0.57" cy="0.25" r="0.2">
        <stop offset="0" stop-color="#e89a3a" stop-opacity="0.8"/>
        <stop offset="1" stop-color="#e89a3a" stop-opacity="0"/>
      </radialGradient>
    </defs>
    <rect width="248" height="156" fill="url(#balloonBase)"/>
    <rect width="248" height="156" fill="url(#balloonGlow)"/>
  </svg>

  <p class="body-copy" style="left:27px; top:462px; width:230px; font-size:12.4px; line-height:14.6px;">
    Each journey is a masterfully curated experience, rich in detail, seamless in execution, and unforgettable in every way.
  </p>

  <svg class="photo photo--framed" role="img" aria-label="Three friends reading a map together on a sunny road trip" style="left:289px; top:60px;" width="231" height="156">
    <defs>
      <linearGradient id="friendsBase" x1="0" y1="0" x2="0" y2="1">
        <stop offset="0" stop-color="#9fc0dc"/>
        <stop offset="0.35" stop-color="#e9eef2"/>
        <stop offset="0.65" stop-color="#dcc3aa"/>
        <stop offset="1" stop-color="#3e4652"/>
      </linearGradient>
      <radialGradient id="friendsCar" cx="0.95" cy="0.85" r="0.3">
        <stop offset="0" stop-color="#c4413b" stop-opacity="0.7"/>
        <stop offset="1" stop-color="#c4413b" stop-opacity="0"/>
      </radialGradient>
    </defs>
    <rect width="231" height="156" fill="url(#friendsBase)"/>
    <rect width="231" height="156" fill="url(#friendsCar)"/>
  </svg>

  <svg class="photo" role="img" aria-label="Traveller in a straw hat with a backpack overlooking a European riverside town" style="left:289px; top:231px;" width="231" height="156">
    <defs>
      <linearGradient id="riverBase" x1="0" y1="0" x2="0" y2="1">
        <stop offset="0" stop-color="#eceae6"/>
        <stop offset="0.4" stop-color="#d3c2a6"/>
        <stop offset="0.7" stop-color="#9c907e"/>
        <stop offset="1" stop-color="#6f6a60"/>
      </linearGradient>
      <radialGradient id="riverHat" cx="0.4" cy="0.35" r="0.3">
        <stop offset="0" stop-color="#d9a465" stop-opacity="0.75"/>
        <stop offset="1" stop-color="#d9a465" stop-opacity="0"/>
      </radialGradient>
    </defs>
    <rect width="231" height="156" fill="url(#riverBase)"/>
    <rect width="231" height="156" fill="url(#riverHat)"/>
  </svg>

  <div class="help-band" style="left:325px; top:375px; width:160px; height:38px; font-size:21px;">Let us help you</div>

  <div class="plan" style="left:403px; top:428px; font-size:15.5px;">Plan your Next Extraordinary</div>
  <div class="adventure" style="left:403px; top:446px; font-size:43px;">Adventure.</div>

  <div class="site" style="left:403px; top:502px; font-size:12.5px; color:var(--brand-blue);">
    <span class="site__dot" style="width:13px; height:13px; background:var(--brand-blue);"></span>tidewelljourneys-example.com
  </div>
</section>

</body>
</html>
```